Looking to Redesign Brevonix.com website

You guys did one of the brochures for brevonix.com and I would like to see if we can go ahead and get an estimate for a redesigned web site for the company. We currently have a couple of pages on brevonix.com which are very much a starter type site.

The new design will need to reflect some of the things discussed in the brochure. It will have flash. Needs to be designed for simple hosting using cpanels.

The site needs to have between 12 and 15 pages with flash pages to move through features. Integrated with twitter like it is now, and contact forms delivered from our CRM along with other interactive features such as subscription to newsletter, etc...

I don't have lots of details on how to proceed yet, but here are some competitor sites:

Can we take a look at potential costs involved in the redo of the site as vague as my description above can permit.

Target Market(s)

Business to Business

Number of Pages Required

5+ page

Font styles to use
Sans Serif

Requirements
Must have
• Must have professional feel. Similar to brochure. and logo.
• Include our story in the discussion.
• embedded links to our CRM for popup contact forms.
• Logo files and 2 types of brochures uploaded.
• Important to keep color scheme
Nice to have
• Flash and some movement
Should not have
• Not sure yet

```html
<!DOCTYPE html>
<html lang="en">
<head>
<meta charset="utf-8">
<title>Brevonix – Benefits</title>
<link rel="stylesheet" href="https://fonts.googleapis.com/css2?family=Raleway:wght@400;500;600;700&family=Arimo:wght@400;700&family=Exo+2:ital,wght@1,800&display=swap">
<style>
:root{
  --red:#c0070d;
  --red-dark:#8f0408;
  --ink:#333333;
  --text:#555555;
  --muted:#8a8f96;
  --line:#d8d8d8;
  --black:#1b1b1b;
  --footer:#3d3d3d;
  --footer-deep:#2a2a2a;
  --white:#ffffff;
}
*{margin:0;padding:0;box-sizing:border-box}
html,body{width:729px;height:1200px;overflow:hidden;background:var(--white)}
body{position:relative;font-family:"Raleway",Arial,sans-serif;color:var(--text)}
.abs{position:absolute}

/* header */
.site-header{position:absolute;left:0;top:0;width:729px;height:92px;background:var(--white);z-index:3}
.brand{position:absolute;left:46px;top:46px;display:flex;align-items:center;gap:7px}
.brand-dot{width:30px;height:30px;border-radius:50%;background:var(--red)}
.brand-name{font-family:"Raleway",sans-serif;font-weight:700;font-size:15px;color:var(--red)}
.contact{position:absolute;top:19px;display:flex;align-items:center;gap:8px}
.contact svg{width:18px;height:18px}
.contact small{display:block;font-size:5.5px;letter-spacing:.4px;color:var(--muted);text-transform:uppercase;margin-bottom:2px}
.contact strong{display:block;font-size:7.5px;font-weight:700;color:var(--ink);letter-spacing:.2px}
.contact.phone strong{font-size:10px}
.contact-sep{position:absolute;top:20px;width:1px;height:22px;background:var(--line)}
.main-nav{position:absolute;top:58px;left:0;width:729px;height:21px}
.main-nav a{position:absolute;top:0;height:21px;line-height:21px;font-size:7.5px;font-weight:700;letter-spacing:.3px;color:var(--ink);text-decoration:none}
.main-nav a.is-active{background:var(--red);color:var(--white);border-radius:11px;padding:0 11px}

/* hero */
.hero-photo{position:absolute;left:0;top:89px;width:729px;height:235px;
  background:linear-gradient(100deg,#d9dcdf 0%,#a9b0b7 28%,#7e8894 52%,#b3bcc6 72%,#8d97a2 100%)}
.waves{position:absolute;left:0;top:0;z-index:1}

/* section headings */
.section-title{position:absolute;left:46px;display:flex;align-items:center;gap:10px;z-index:2}
.section-mark{width:28px;height:22px;border-radius:50%;background:#c3c3c3}
.section-title h2{font-family:"Exo 2",sans-serif;font-style:italic;font-weight:800;font-size:18px;color:var(--red);letter-spacing:.3px}
.intro{position:absolute;left:46px;top:385px;font-size:10.5px;color:var(--ink);font-weight:500}

/* benefits */
.benefit{position:absolute;display:flex;gap:18px;z-index:2}
.benefit-icon{flex:none;width:42px;height:42px;border:1px solid #3a3a3a;border-radius:50%;display:flex;align-items:center;justify-content:center}
.benefit-icon svg{width:15px;height:15px;fill:var(--red)}
.benefit h3{font-family:"Arimo",Arial,sans-serif;font-weight:400;font-size:10.5px;color:var(--red);margin:6px 0 3px}
.benefit p{font-family:"Arimo",Arial,sans-serif;font-size:8.5px;line-height:14px;color:var(--text)}

/* features */
.feature-list{position:absolute;list-style:none;font-family:"Arimo",Arial,sans-serif;font-size:8.8px;line-height:14.5px;color:var(--text);z-index:2}
.feature-list li{position:relative;padding-left:12px;margin-bottom:5px}
.feature-list li::before{content:"";position:absolute;left:0;top:3px;width:7px;height:7px;border-radius:50%;background:var(--red)}
.feature-list li::after{content:"";position:absolute;left:2px;top:4.5px;width:2.5px;height:1.5px;border-left:1px solid #fff;border-bottom:1px solid #fff;transform:rotate(-45deg)}

/* footer */
.footer{position:absolute;left:0;top:1010px;width:729px;z-index:2;color:#e8e8e8}
.footer-brand{position:absolute;left:46px;top:20px;display:flex;align-items:center;gap:7px}
.footer-brand .brand-dot{background:var(--white)}
.footer-brand .brand-name{color:var(--white)}
.footer-about{position:absolute;left:46px;top:76px;font-size:8.5px;line-height:15px;color:#eee;width:180px}
.read-more{position:absolute;left:46px;top:112px;font-size:8.5px;font-weight:700;color:var(--white)}
.footer-divider{position:absolute;top:14px;width:1px;height:112px;background:#2c2c2c;box-shadow:1px 0 0 #4a4a4a}
.footer h4{position:absolute;top:18px;font-size:8.5px;font-weight:700;letter-spacing:.4px;color:var(--white)}
.quick-links a{position:absolute;font-size:8px;color:#ddd;text-decoration:none}
.news-input{position:absolute;left:507px;width:177px;height:22px;border-radius:11px;background:var(--white);font-size:8px;color:#666;padding-left:14px;line-height:22px}
.signup{position:absolute;left:614px;top:97px;width:70px;height:22px;border-radius:11px;background:linear-gradient(#d50b12,var(--red-dark));color:var(--white);font-size:8.5px;font-weight:600;text-align:center;line-height:22px}
.bottom-bar{position:absolute;left:0;top:1156px;width:729px;height:44px;background:linear-gradient(#2d2d2d,#3a3a3a);z-index:2}
.copyright{position:absolute;left:46px;top:17px;font-size:7.5px;color:#bbb}
.social{position:absolute;top:14px;width:18px;height:18px;border-radius:50%;background:#2b8fd0}
</style>
</head>
<body>

<header class="site-header">
  <div class="brand"><span class="brand-dot"></span><span class="brand-name">brevonix</span></div>

  <div class="contact" style="left:310px">
    <svg viewBox="0 0 20 20"><circle cx="10" cy="6" r="4.5" fill="#222"/><path d="M2 19c0-5 3.5-7 8-7s8 2 8 7z" fill="#222"/></svg>
    <div><small>Support</small><strong>CHAT WITH US</strong></div>
  </div>
  <span class="contact-sep" style="left:415px"></span>
  <div class="contact" style="left:429px">
    <svg viewBox="0 0 20 20"><rect x="2" y="4" width="16" height="12" fill="none" stroke="#222" stroke-width="1.6"/><path d="M2 4l8 7 8-7" fill="none" stroke="#222" stroke-width="1.6"/></svg>
    <div><small>Email us at</small><strong>SALES@BREVONIX.COM</strong></div>
  </div>
  <span class="contact-sep" style="left:569px"></span>
  <div class="contact phone" style="left:583px">
    <svg viewBox="0 0 20 20"><path d="M5 2l3 4-2 2c1 2.5 3 4.5 5.5 5.5l2-2 4 3-2 3.5C9 17 3 11 1.5 4.5z" fill="#222"/></svg>
    <div><small>Call us now</small><strong>+1 800 555 0142</strong></div>
  </div>

  <nav class="main-nav">
    <a style="left:254px">HOME</a>
    <a style="left:304px">WHY BREVONIX</a>
    <a class="is-active" style="left:391px">BENEFITS</a>
    <a style="left:469px">CASE STUDIES</a>
    <a style="left:555px">HARDWARE</a>
    <a style="left:630px">ABOUT US</a>
  </nav>
</header>

<div class="hero-photo" role="img" aria-label="Photo of a businessman drawing a cloud network diagram with a computer and arrows"></div>

<svg class="waves" width="729" height="1200" viewBox="0 0 729 1200" aria-hidden="true">
  <defs>
    <linearGradient id="footerGrad" x1="0" y1="0" x2="0" y2="1">
      <stop offset="0" stop-color="#4a4a4a"/>
      <stop offset="1" stop-color="#2f2f2f"/>
    </linearGradient>
  </defs>
  <!-- hero edge -->
  <path d="M0,258 C160,244 380,262 729,292 L729,340 L0,340Z" fill="var(--red)"/>
  <path d="M0,263 C160,250 380,268 729,300 L729,340 L0,340Z" fill="var(--black)"/>
  <path d="M0,282 C170,266 400,286 729,320 L729,340 L0,340Z" fill="var(--white)"/>
  <!-- divider between benefits and features -->
  <path d="M0,618 C110,606 360,626 729,648 L729,668 C360,648 110,630 0,642Z" fill="var(--black)"/>
  <path d="M0,614 C110,602 360,622 729,646 L729,652 C360,630 110,612 0,626Z" fill="var(--red)"/>
  <!-- footer top -->
  <path d="M0,896 C240,928 480,955 729,956 L729,1010 L0,1010Z" fill="var(--red)"/>
  <path d="M0,918 C260,948 500,990 729,994 L729,1200 L0,1200Z" fill="var(--black)"/>
  <path d="M0,934 C260,962 500,1004 729,1008 L729,1200 L0,1200Z" fill="url(#footerGrad)"/>
</svg>

<!-- benefits -->
<div class="section-title" style="top:347px"><span class="section-mark"></span><h2>BENEFITS</h2></div>
<p class="intro">Discovering your needs, creating solutions that truly work</p>

<div class="benefit" style="left:46px;top:413px">
  <span class="benefit-icon"><svg viewBox="0 0 16 16"><path d="M3 1h7l3 3v11H3z"/><rect x="5" y="7" width="6" height="1.2" fill="#fff"/><rect x="5" y="9.5" width="6" height="1.2" fill="#fff"/><rect x="5" y="12" width="6" height="1.2" fill="#fff"/></svg></span>
  <div><h3>Quick ROI</h3><p>Equipment is included in the ser-<br>vice..</p></div>
</div>
<div class="benefit" style="left:288px;top:413px">
  <span class="benefit-icon"><svg viewBox="0 0 16 16"><path d="M5 7V5a3 3 0 0 1 6 0v2h-1.6V5a1.4 1.4 0 0 0-2.8 0v2z"/><rect x="3.5" y="7" width="9" height="7" rx="1"/></svg></span>
  <div><h3>Secure</h3><p>Encrypted lines</p></div>
</div>
<div class="benefit" style="left:482px;top:413px">
  <span class="benefit-icon"><svg viewBox="0 0 16 16"><rect x="6" y="1" width="4" height="4"/><rect x="1" y="11" width="4" height="4"/><rect x="6" y="11" width="4" height="4"/><rect x="11" y="11" width="4" height="4"/><path d="M7.5 5h1v3h5v3h-1V9h-4v2h-1V9h-4v2h-1V8h5z"/></svg></span>
  <div><h3>Intuitive</h3><p>Easy to learn and run</p></div>
</div>

<div class="benefit" style="left:46px;top:473px">
  <span class="benefit-icon"><svg viewBox="0 0 16 16"><circle cx="6" cy="9" r="4" /><circle cx="6" cy="9" r="1.5" fill="#fff"/><circle cx="12" cy="4" r="2.6"/><circle cx="12" cy="4" r="1" fill="#fff"/><circle cx="12.5" cy="12" r="2"/></svg></span>
  <div><h3>Easy installation</h3><p>Very little business<br>interruption</p></div>
</div>
<div class="benefit" style="left:288px;top:473px">
  <span class="benefit-icon"><svg viewBox="0 0 16 16"><circle cx="8" cy="8" r="7"/><circle cx="8" cy="8" r="5.3" fill="#fff"/><path d="M7.3 4h1.4v3.6H11V9H7.3z"/></svg></span>
  <div><h3>Expandable</h3><p>One unit at a time</p></div>
</div>
<div class="benefit" style="left:482px;top:473px">
  <span class="benefit-icon"><svg viewBox="0 0 16 16"><path d="M4 1l2.6 3.4-1.7 1.7c.9 2 2.5 3.6 4.5 4.5l1.7-1.7L14.5 11.5l-1.7 3C7 14.5 1.5 9 1.5 3.2z"/></svg></span>
  <div><h3>Fail-over</h3><p>Calls go through even if a<br>supplier phone company has out-<br>ages</p></div>
</div>

<div class="benefit" style="left:46px;top:543px">
  <span class="benefit-icon"><svg viewBox="0 0 16 16"><path d="M8 2a6 6 0 0 1 5.5 3.6L15 4v5h-5l1.8-1.8A4 4 0 0 0 4.2 7H2.1A6 6 0 0 1 8 2z"/><path d="M8 14a6 6 0 0 1-5.5-3.6L1 12V7h5L4.2 8.8A4 4 0 0 0 11.8 9h2.1A6 6 0 0 1 8 14z"/></svg></span>
  <div><h3>Customized</h3><p>Expandable speed-dial options</p></div>
</div>
<div class="benefit" style="left:288px;top:543px">
  <span class="benefit-icon"><svg viewBox="0 0 16 16"><path d="M2 2h12v6c0 3.5-2.8 5.7-6 7-3.2-1.3-6-3.5-6-7z"/><path d="M8 4.5h3.5V8c0 2-1.4 3.3-3.5 4.2z" fill="#fff"/></svg></span>
  <div><h3>Safety</h3><p>911 notification to managers</p></div>
</div>

<!-- features -->
<div class="section-title" style="top:699px"><span class="section-mark"></span><h2>FEATURES</h2></div>

<ul class="feature-list" style="left:49px;top:736px;width:300px">
  <li>Integrated phone services for one desk to 100 and beyond</li>
  <li>Work wherever you or your employees are – from home, the office,<br>the beach! Brevonix follows you</li>
  <li>Flexible system designed for the unique needs of your company</li>
  <li>Connect multiple locations into one system</li>
  <li>No huge investments, Brevonix provides the system, just<br>“plug and play”</li>
  <li>Easy to add one station at a time as your business grows</li>
</ul>

<ul class="feature-list" style="left:377px;top:736px;width:320px">
  <li>Expand employee options by setting up work-at-home station</li>
  <li>Tech support that responds promptly, and personally</li>
  <li>Secure, encrypted technology</li>
  <li>Automated call routing based on location of incoming calls.<br>(Not only based on location but a wide variety of rules that are chosen<br>by the client)</li>
  <li>Programmable speed dialing</li>
</ul>

<!-- footer -->
<footer class="footer">
  <div class="footer-brand"><span class="brand-dot"></span><span class="brand-name">brevonix</span></div>
  <p class="footer-about">Inter-Company Cloud Communications<br>Platform..</p>
  <span class="read-more">Read More</span>

  <span class="footer-divider" style="left:264px"></span>
  <span class="footer-divider" style="left:490px"></span>

  <h4 style="left:282px">QUICK LINKS</h4>
  <nav class="quick-links">
    <a style="left:282px;top:36px">Home</a>
    <a style="left:282px;top:55px">Why Brevonix</a>
    <a style="left:282px;top:73px">Benefits</a>
    <a style="left:282px;top:92px">Case Studies</a>
    <a style="left:383px;top:36px">Hardware</a>
    <a style="left:383px;top:55px">About Us</a>
    <a style="left:383px;top:73px">Contact Us</a>
  </nav>

  <h4 style="left:510px">NEWSLETTER SIGN UP</h4>
  <div class="news-input" style="top:38px">Enter Name</div>
  <div class="news-input" style="top:66px">Enter Email Address</div>
  <div class="signup">SIGN UP</div>
</footer>

<div class="bottom-bar">
  <p class="copyright">© 2015-2016 brevonix. All Rights Reserved.</p>
  <span class="social" style="left:643px"></span>
  <span class="social" style="left:666px"></span>
</div>

</body>
</html>
```